Electric mountain bike tours nz

We are an Electric Mountain bike tour company in New Zealand. We will be offering bike rental and guided tours around the Nelson region in New Zealand. I want our website to represent both Mountain biking and New Zealand with the colours layout and features. We want tabs for the following:
-1 about us
-2 what we offer
-3 bookings/contact
Under the about us tab will be who we are as a a company. I want the ability to add videos to each of these tabs as we move foward with videos of the tracks we will be riding. I want the website to be editable so I can add and remove videos/photos myself. Also "our bikes" will be under this tab.
Under the what we offer tab will be
-1 bike rental and pricing
-2 guided tours and pricing
-3 recommended package deals.
I want to able to put the tracks under the guided tours tab and select beginner/ intermediate/advanced and have the tracks in each of the following to match the rider level. Also to be able to have a small video of the track would be great in this section.
Bookings and contact tab
(Further information for this tab to be updated soon)
Coded - Design and coding required
1 page
- Silver ferns, kiwi, mountains

```html
<!DOCTYPE html>
<html lang="en">
<head>
<meta charset="utf-8">
<title>Ridgeline NZ – Bike Rental &amp; Guided Tours</title>
<link href="https://fonts.googleapis.com/css2?family=Mulish:wght@400;600;700;800;900&family=Open+Sans:wght@400;600;700&display=swap" rel="stylesheet">
<style>
:root{
  --green:#1fbf74;
  --green-dark:#17a863;
  --blue:#2f6fd0;
  --navy:#1f4e9e;
  --ink:#2b2b2b;
  --muted:#7a7a7a;
  --light:#f4f4f4;
  --line:#d6d6d6;
  --white:#ffffff;
}
*{box-sizing:border-box;margin:0;padding:0}
html,body{width:1200px;height:3922px;overflow:hidden}
body{position:relative;font-family:"Open Sans",sans-serif;color:var(--ink);background:var(--white)}
.abs{position:absolute}
h1,h2,h3,.head{font-family:"Mulish",sans-serif}
.section-title{position:absolute;font-family:"Mulish",sans-serif;font-weight:800;font-size:31px;color:var(--blue)}
.center{left:0;width:1200px;text-align:center}
.btn{position:absolute;display:flex;align-items:center;justify-content:center;background:var(--green);color:var(--white);font-family:"Mulish",sans-serif;font-weight:700;border-radius:4px}

/* hero */
.hero{position:absolute;left:0;top:0;width:1200px;height:655px;background:linear-gradient(180deg,#5d7380 0%,#3e4a3e 45%,#2c2a22 100%)}
.hero-photo{position:absolute;inset:0;background:linear-gradient(180deg,rgba(30,30,30,.15),rgba(20,20,20,.45))}
.brand{position:absolute;left:100px;top:22px;display:flex;align-items:center;gap:12px;font-family:"Mulish",sans-serif;font-weight:800;font-size:26px;color:var(--white)}
.brand-dot{width:18px;height:18px;border-radius:50%;background:var(--white)}
.call{left:740px;top:30px;color:var(--white);font-family:"Mulish",sans-serif;font-weight:700;font-size:17px}
.nav{position:absolute;left:585px;top:80px;display:flex;gap:18px;font-family:"Mulish",sans-serif;font-weight:700;font-size:16px;color:var(--white)}
.hero-kicker{left:100px;top:258px;color:var(--white);font-family:"Mulish",sans-serif;font-weight:800;font-size:30px}
.hero-title{left:97px;top:302px;color:var(--white);font-family:"Mulish",sans-serif;font-weight:900;font-size:49px;line-height:62px}

/* search */
.tab{position:absolute;z-index:5;top:508px;height:40px;display:flex;align-items:center;justify-content:center;font-family:"Mulish",sans-serif;font-weight:600;font-size:15px}
.search{position:absolute;z-index:5;left:86px;top:548px;width:1025px;height:171px;background:var(--white);box-shadow:0 4px 14px rgba(0,0,0,.15)}
.field-label{position:absolute;top:30px;font-family:"Mulish",sans-serif;font-weight:700;font-size:15px}
.input{position:absolute;top:66px;height:32px;border:1px solid var(--line);border-radius:2px;font-size:12px;color:var(--muted);display:flex;align-items:center;padding-left:10px}
.hot{position:absolute;left:52px;top:124px;display:flex;gap:30px;font-size:14px;color:var(--ink)}
.hot b{font-family:"Mulish",sans-serif;font-weight:700}
.hot .on{color:var(--green)}

/* about */
.about{position:absolute;left:0;top:655px;width:1200px;height:495px;background:var(--light)}
.about-text{left:172px;width:352px;font-size:13px;line-height:26px;color:var(--muted)}

/* places */
.places-bg{position:absolute;left:0;top:1150px;width:1200px;height:785px;background:var(--white)}
.para{position:absolute;font-size:12.5px;line-height:24px;color:var(--muted)}
.tile{position:absolute;display:flex;align-items:flex-end;padding:0 0 14px 34px;color:var(--white);font-family:"Mulish",sans-serif;font-weight:800;font-size:14px}

/* why */
.why{position:absolute;left:0;top:1935px;width:1200px;height:483px;background:var(--light)}
.feature{position:absolute;top:195px;width:300px;text-align:center}
.ring{width:130px;height:130px;margin:0 auto;border-radius:50%;border:3px solid var(--blue);display:flex;align-items:center;justify-content:center;background:var(--white)}
.ring-in{width:104px;height:104px;border-radius:50%;border:1px solid #c9d6ec;display:flex;align-items:center;justify-content:center}
.feature h3{margin-top:22px;font-weight:700;font-size:17px}
.feature p{margin-top:6px;font-size:13px;line-height:22px;color:var(--muted)}

/* packages */
.pk-band{position:absolute;left:0;top:2418px;width:1200px;height:330px;background:linear-gradient(180deg,#e9e9e9,#f6f6f6)}
.pk-tab{position:absolute;top:2515px;height:30px;display:flex;align-items:center;justify-content:center;font-family:"Mulish",sans-serif;font-weight:700;font-size:13px;background:var(--blue);color:var(--white)}
.card{position:absolute;top:2604px;width:303px;height:371px;background:var(--navy);color:var(--white);padding:26px 30px}
.card h3{font-weight:800;font-size:19px;white-space:nowrap}
.stars{margin-top:10px;display:flex;align-items:center;gap:3px;font-size:12px}
.star{width:14px;height:14px;background:var(--green)}
.meta{margin-top:10px;font-size:12px}
.ticks{margin-top:18px;list-style:none;font-size:12px;line-height:25px}
.ticks li::before{content:"✓";color:var(--green);margin-right:8px;font-weight:700}
.from{margin-top:18px;font-size:13px;color:var(--green)}
.price{font-family:"Mulish",sans-serif;font-weight:800;font-size:20px;color:var(--green);white-space:nowrap}
.card .btn{position:static;margin-top:18px;width:120px;height:36px;font-size:15px}

/* contact */
.contact{position:absolute;left:0;top:3085px;width:1200px;height:522px;background:var(--green)}
.c-field{position:absolute;border:1px solid rgba(255,255,255,.85);color:var(--white);font-size:13px;padding:10px 12px}

/* footer */
.f-head{position:absolute;top:3668px;font-family:"Mulish",sans-serif;font-weight:700;font-size:17px}
.f-text{position:absolute;font-size:12.5px;line-height:22px;color:var(--ink)}
</style>
</head>
<body>

<!-- HERO -->
<header class="hero">
  <div class="hero-photo" role="img" aria-label="Photo of a red mountain bike on a trail above a coastal bay"></div>
  <div class="brand"><span class="brand-dot"></span>Ridgeline NZ</div>
  <div class="abs call">Call Us: (+1) 555 010 0199</div>
  <div class="btn" style="left:993px;top:24px;width:105px;height:34px;font-size:15px">Book Now</div>
  <nav class="nav"><span>HOME</span><span>ABOUT US</span><span>WHAT WE OFFER</span><span>BOOKINGS</span><span>CONTACT US</span></nav>
  <div class="abs hero-kicker">NEW ZEALAND</div>
  <h1 class="abs hero-title">BIKE RENTAL &amp; GUIDED TOURS<br>IN NELSON REGION</h1>
</header>

<div class="tab" style="left:86px;width:167px;background:var(--white)">BIKE RENTAL</div>
<div class="tab" style="left:267px;width:164px;background:#cfc6bc;color:var(--white)">GUIDED TOURS</div>

<!-- ABOUT -->
<section class="about">
  <h2 class="section-title" style="left:172px;top:125px">About Us</h2>
  <p class="abs about-text" style="top:175px">We are a company specialized in the rental of last generation motor bikes for your vacations and expeditions throughout New Zealand.<br>Nam libero tempore, cum soluta nobis est eligendi optio cumque nihil impedit quo minus id quod maxime placeat facere possimus, omnis voluptas assumenda est, omnis dolor repel lendus necessitatibus saepe voluptates repudiandae.</p>
  <div class="btn" style="left:172px;top:380px;width:116px;height:36px;font-size:14px">Read More</div>
  <div class="abs" role="img" aria-label="Photo of a black electric mountain bike" style="left:588px;top:145px;width:497px;height:280px;border-radius:6px;background:linear-gradient(180deg,#e4e4e4,#cfcfcf)"></div>
</section>

<section class="search">
  <div class="field-label" style="left:52px">SOURCE</div>
  <div class="field-label" style="left:228px">DESTINATION</div>
  <div class="field-label" style="left:403px">STARTING TIME</div>
  <div class="field-label" style="left:620px">RETURN</div>
  <div class="input" style="left:52px;width:146px">Select Country ⌄</div>
  <div class="input" style="left:228px;width:146px">Select Location ⌄</div>
  <div class="input" style="left:403px;width:100px">Date ▦</div>
  <div class="input" style="left:510px;width:90px">Time ◷</div>
  <div class="input" style="left:620px;width:100px">Date ▦</div>
  <div class="input" style="left:727px;width:90px">Time ◷</div>
  <div class="btn" style="left:842px;top:58px;width:133px;height:42px;font-size:18px">Search</div>
  <div class="hot"><b>HOT DESTINATIONS ›</b><span class="on">Abel Tasman</span><span>Kahurangi</span><span>Nelson Haven</span><span>Lake Rotoiti</span><span>Great Taste Trail</span><span>Boulder Bank</span><span>Mount Owen</span></div>
</section>

<!-- POPULAR PLACES -->
<section class="places-bg"></section>
<h2 class="section-title center" style="top:1228px">Popular Places</h2>
<p class="para center" style="top:1280px">In Nelson, we are the local partner of the Southern Trail Collective, a leading guided cycling network in the region,<br>for the Kereru Cycles brand. Alongside this, we also represent the Tui and Matai e-bike brands.</p>
<div class="tile" role="img" aria-label="Photo of a snow-capped volcano above forest" style="left:230px;top:1359px;width:484px;height:314px;background:linear-gradient(180deg,#5c93d6 0%,#b7cde3 45%,#3d6a3b 75%,#2a4a28 100%)">MOUNT TARANAKI</div>
<div class="tile" role="img" aria-label="Photo of snowy alpine peaks" style="left:724px;top:1359px;width:238px;height:314px;background:linear-gradient(180deg,#3f78c5,#a9c2dc 50%,#7e7a55 80%,#5b5a3c)">MOUNT COOK</div>
<div class="tile" role="img" aria-label="Photo of a lake among mountains" style="left:230px;top:1681px;width:238px;height:157px;background:linear-gradient(180deg,#8fb3d8,#6c8ea5 50%,#8a7a52)">ROYS PEAK</div>
<div class="abs" style="left:478px;top:1681px;width:236px;height:157px;background:var(--blue);color:var(--white);padding:16px 16px">
  <div style="font-family:'Mulish',sans-serif;font-weight:800;font-size:14px">FOUNDERS HERITAGE PARK</div>
  <p style="font-size:9.5px;line-height:15px;margin-top:8px;opacity:.9">A heritage village of old shops and cottages near the city, with a brewery, café and gentle paths, ideal for an easy ride with family.</p>
  <div style="font-size:11px;margin-top:8px">Learn More</div>
</div>
<div class="tile" role="img" aria-label="Photo of a road leading toward snowy mountains" style="left:724px;top:1681px;width:238px;height:157px;background:linear-gradient(180deg,#7fa4cf,#c9d4dc 45%,#6f6b52 80%,#4a473a)">SOUTHERN ALPS</div>
<div class="abs" role="img" aria-label="Illustration of a kiwi bird beside a bicycle" style="left:1005px;top:1790px;width:190px;height:150px;border-radius:8px;background:linear-gradient(180deg,#a27c56,#6e4e30)"></div>

<!-- WHY US -->
<section class="why">
  <h2 class="section-title center" style="top:68px">Why Us</h2>
  <p class="para center" style="top:118px">In Nelson, we are the local partner of the Southern Trail Collective, a leading guided cycling network in the region,<br>for the Kereru Cycles brand. Alongside this, we also represent the Tui and Matai e-bike brands.</p>
  <div class="feature" style="left:140px">
    <div class="ring"><div class="ring-in"><svg width="40" height="40" viewBox="0 0 24 24" fill="var(--blue)"><path d="M2 10h4v11H2zM8 21h9.5a2 2 0 0 0 2-1.6l1.4-7A2 2 0 0 0 19 10h-5.5l.8-4a2 2 0 0 0-3.6-1.4L8 9.5z"/></svg></div></div>
    <h3>FAIR</h3><p>Drive into your holiday with the vehicle<br>group you have requested</p>
  </div>
  <div class="feature" style="left:443px">
    <div class="ring"><div class="ring-in"><svg width="40" height="40" viewBox="0 0 24 24" fill="none" stroke="var(--blue)" stroke-width="2"><circle cx="12" cy="12" r="10"/><circle cx="9" cy="10" r=".6" fill="var(--blue)"/><circle cx="15" cy="10" r=".6" fill="var(--blue)"/><path d="M7.5 14a5 5 0 0 0 9 0"/></svg></div></div>
    <h3>EASY</h3><p>A good choice between different groups of<br>vehicles at reasonable prices</p>
  </div>
  <div class="feature" style="left:747px">
    <div class="ring"><div class="ring-in"><svg width="36" height="40" viewBox="0 0 24 26" fill="var(--blue)"><path d="M12 1 2 5v7c0 6.5 4.3 11.5 10 13 5.7-1.5 10-6.5 10-13V5z"/><path d="M12 4v19c-4-1.4-7-5.2-7-10V7z" fill="#fff"/></svg></div></div>
    <h3>SAFE</h3><p>New models of vehicle with secure planning<br>and mobility warranty</p>
  </div>
</section>

<!-- PACKAGES -->
<div class="pk-band" role="img" aria-label="Faint silver fern leaves in the background"></div>
<h2 class="section-title" style="left:100px;top:2506px;color:var(--blue)">Our Packages</h2>
<div class="pk-tab" style="left:698px;width:94px">Bike Rental</div>
<div class="pk-tab" style="left:810px;width:108px;background:var(--white);color:var(--blue)">Guided Tours</div>
<div class="pk-tab" style="left:936px;width:162px">Recommended Rental</div>

<article class="card" style="left:100px">
  <h3>Abel Tasman Packages</h3>
  <div class="stars"><span class="star"></span><span class="star"></span><span class="star"></span><span class="star"></span><span class="star"></span>&nbsp;81 ratings</div>
  <div class="meta">◷ 1 Day, ⚲ Abel Tasman</div>
  <ul class="ticks"><li>Sprintelio Booking Fees</li><li>SprintMoney Safe Guarantee</li><li>Sprintinstant Confirmation Voucher</li></ul>
  <div class="from">Starting From</div><div class="price">$1,600 &nbsp;$1,400 per day</div>
  <div class="btn">Book Now</div>
</article>
<article class="card" style="left:450px">
  <h3>Kahurangi Packages</h3>
  <div class="stars"><span class="star"></span><span class="star"></span><span class="star"></span><span class="star"></span><span class="star"></span>&nbsp;78 ratings</div>
  <div class="meta">◷ 1 Day, ⚲ Abel Tasman</div>
  <ul class="ticks"><li>Sprintelio Booking Fees</li><li>SprintMoney Safe Guarantee</li><li>Sprintinstant Confirmation Voucher</li></ul>
  <div class="from">Starting From</div><div class="price">$1,500 &nbsp;$1,250 per day</div>
  <div class="btn">Book Now</div>
</article>
<article class="card" style="left:797px">
  <h3>Lake Rotoiti Packages</h3>
  <div class="stars"><span class="star"></span><span class="star"></span><span class="star"></span><span class="star"></span><span class="star"></span>&nbsp;92 ratings</div>
  <div class="meta">◷ 1 Day, ⚲ Abel Tasman</div>
  <ul class="ticks"><li>Sprintelio Booking Fees</li><li>SprintMoney Safe Guarantee</li><li>Sprintinstant Confirmation Voucher</li></ul>
  <div class="from">Starting From</div><div class="price">$1,7500 &nbsp;$1,500 per day</div>
  <div class="btn">Book Now</div>
</article>

<!-- CONTACT -->
<section class="contact">
  <h2 class="abs head" style="left:100px;width:517px;top:70px;text-align:center;color:var(--white);font-weight:800;font-size:31px">Contact Us</h2>
  <p class="abs" style="left:100px;width:517px;top:120px;text-align:center;color:var(--white);font-size:14px">Speak With One Of Our Expert About Your Expectation</p>
  <div class="c-field" style="left:100px;top:175px;width:243px;height:37px">First Name</div>
  <div class="c-field" style="left:374px;top:175px;width:243px;height:37px">Last Name</div>
  <div class="c-field" style="left:100px;top:237px;width:243px;height:37px">Phone No</div>
  <div class="c-field" style="left:374px;top:237px;width:243px;height:37px">Email Id</div>
  <div class="c-field" style="left:100px;top:303px;width:517px;height:81px">Message</div>
  <div class="abs head" style="left:227px;top:410px;width:272px;height:39px;border:2px solid var(--white);border-radius:4px;color:var(--white);font-weight:700;font-size:16px;display:flex;align-items:center;justify-content:center">Talk with an Expert Today!</div>
  <div class="abs" role="img" aria-label="Video still of a rider on a mountain bike trail" style="left:656px;top:120px;width:445px;height:266px;border:3px solid var(--white);background:linear-gradient(160deg,#6f7a3c,#4f5a2c 50%,#8a7a4a)"></div>
  <div class="abs" style="left:851px;top:226px;width:54px;height:54px;border-radius:50%;background:var(--white);display:flex;align-items:center;justify-content:center"><svg width="22" height="22" viewBox="0 0 10 10"><path d="M2 1l7 4-7 4z" fill="var(--green)"/></svg></div>
  <div class="abs head" style="left:656px;width:445px;top:403px;text-align:center;color:var(--white);font-weight:800;font-size:17px">Watch Our Video</div>
</section>

<!-- FOOTER -->
<footer>
  <div class="abs head" style="left:115px;top:3735px;display:flex;align-items:center;gap:10px;font-weight:800;font-size:24px;color:var(--ink)"><span style="width:16px;height:16px;border-radius:50%;background:var(--ink)"></span>Ridgeline NZ</div>
  <div class="f-head" style="left:358px">Contact</div>
  <div class="f-text" style="left:362px;top:3705px">⚲ Electric mountain bike tours,<br>&nbsp;&nbsp;&nbsp;Nelson, New Zealand.</div>
  <div class="f-text" style="left:362px;top:3763px">✉ hello@ridgelinenz.com</div>
  <div class="f-text" style="left:362px;top:3788px">✆ Phone: (+1) 555 010 0199</div>
  <div class="f-head" style="left:630px">Newsletter Subscribe</div>
  <div class="f-text" style="left:630px;top:3700px;color:var(--muted)">Lorem Ipsum is simply dummy text of the<br>printing industry.</div>
  <div class="abs" style="left:630px;top:3765px;width:252px;height:38px;border:1px solid var(--line);font-size:12px;color:var(--muted);padding:10px 12px">Your Email Address <span style="float:right;color:var(--green)">✉</span></div>
  <div class="f-head" style="left:957px">Follow Us On</div>
  <div class="abs" style="left:960px;top:3706px;display:flex;gap:16px">
    <span style="width:16px;height:16px;border-radius:50%;background:var(--green)"></span>
    <span style="width:16px;height:16px;border-radius:50%;background:var(--green)"></span>
    <span style="width:16px;height:16px;border-radius:50%;background:var(--green)"></span>
    <span style="width:16px;height:16px;border-radius:50%;background:var(--green)"></span>
  </div>
  <div class="abs" role="img" aria-label="Green silver fern fronds" style="left:940px;top:3760px;width:200px;height:162px;border-radius:8px 8px 0 0;background:linear-gradient(180deg,#8fd07a,#3f9a3a)"></div>
  <div class="abs" style="left:100px;top:3864px;width:1000px;height:1px;background:var(--line)"></div>
  <div class="f-text center" style="top:3878px;font-size:12px">Copyright © 2018 All Rights Reserved.</div>
</footer>

</body>
</html>
```